Rack Card Design Project

We are a locally family owned public golf course. We would like to have a rack card designed that can be used for multiple applications. The colors in our logo are grey, blue, and white. Please use those in the card design. The company logo, contact information, address, and summer pricing should be included. I've included some pictures that may or may not be used. I'm also open to suggestions....use one photo, multiple photos, a stock photo or image representing golf etc.

```html
<!DOCTYPE html>
<html lang="en">
<head>
<meta charset="utf-8">
<title>Summer Rates Rack Card</title>
<link rel="stylesheet" href="https://fonts.googleapis.com/css2?family=Barlow+Condensed:wght@600;700&family=Source+Sans+3:wght@300;400;700&display=swap">
<style>
  :root {
    --navy: #0d2a5c;
    --navy-deep: #0a2150;
    --blue: #1f54a8;
    --sky-top: #3f6fbf;
    --sky-mid: #6f9fdc;
    --grass: #3f7a2c;
    --grass-light: #7aa457;
    --grey: #8f9296;
    --grey-light: #a5a8ac;
    --text-dark: #2f3338;
    --white: #ffffff;
    --page: #e9eaec;
  }
  * { margin: 0; padding: 0; box-sizing: border-box; }
  html, body { width: 693px; height: 1200px; overflow: hidden; background: var(--page); }
  .rack-card {
    position: absolute; left: 70px; top: 0; width: 553px; height: 1200px;
    background: var(--white); overflow: hidden;
    font-family: "Source Sans 3", sans-serif;
  }
  .hero-photo {
    position: absolute; left: 0; top: 0; width: 553px; height: 720px;
    background: linear-gradient(180deg, var(--sky-top) 0%, var(--sky-mid) 48%, #9cc2e6 58%, var(--grass-light) 64%, var(--grass) 82%, #2f6422 100%);
  }
  .hero-curve { position: absolute; left: 0; top: 610px; width: 553px; height: 120px; }
  .lower-fade {
    position: absolute; left: 0; top: 880px; width: 553px; height: 160px;
    background: linear-gradient(180deg, rgba(255,255,255,0) 0%, rgba(205,218,228,.55) 100%);
  }
  .title {
    position: absolute; top: 52px; width: 100%; text-align: center;
    font-family: "Barlow Condensed", sans-serif; font-weight: 700;
    font-size: 70px; line-height: 1; color: var(--white);
    text-shadow: 0 3px 6px rgba(0,0,0,.35);
  }
  .dates {
    position: absolute; top: 142px; width: 100%; text-align: center;
    font-family: "Barlow Condensed", sans-serif; font-weight: 700;
    font-size: 30px; color: var(--navy);
  }
  .club-seal {
    position: absolute; left: 288px; top: 568px; width: 234px; height: 234px;
    border-radius: 50%; background: var(--grey-light);
    display: flex; align-items: center; justify-content: center; text-align: center;
    font-family: "Barlow Condensed", sans-serif; font-weight: 700;
    font-size: 30px; line-height: 1.1; color: var(--navy); padding: 30px;
    box-shadow: 0 3px 8px rgba(0,0,0,.25);
  }
  .rate-tab {
    position: absolute; left: 0; width: 276px; height: 33px;
    background: linear-gradient(90deg, var(--blue), var(--navy-deep));
    border-radius: 0 17px 17px 0;
    font-family: "Barlow Condensed", sans-serif; font-weight: 700;
    font-size: 26px; line-height: 33px; color: var(--white); padding-left: 32px;
    box-shadow: 2px 3px 5px rgba(0,0,0,.3);
  }
  .tab-full { top: 747px; }
  .tab-nine { top: 917px; }
  .rate-list { position: absolute; left: 31px; list-style: none; color: var(--text-dark); font-size: 19px; font-weight: 300; }
  .rate-list li { height: 33px; line-height: 33px; }
  .rate-list b { font-weight: 700; }
  .rates-full { top: 790px; }
  .rates-nine { top: 956px; }
  .children-note {
    position: absolute; left: 300px; top: 838px; width: 212px; text-align: center;
    font-family: "Barlow Condensed", sans-serif; font-weight: 700;
    font-size: 26px; line-height: 32px; color: var(--navy);
  }
  .lunch {
    position: absolute; left: 31px; top: 997px;
    font-family: "Barlow Condensed", sans-serif; font-weight: 700;
    font-size: 25px; color: #3d4146;
  }
  .address-band {
    position: absolute; left: 0; top: 1043px; width: 553px; height: 76px;
    background: linear-gradient(90deg, var(--blue), var(--navy-deep));
    color: var(--white); text-align: center; font-size: 21px; font-weight: 300;
    line-height: 30px; padding-top: 8px;
  }
  .contact-bar {
    position: absolute; left: 0; top: 1121px; width: 553px; height: 79px;
    background: var(--grey); display: flex; align-items: center; justify-content: space-around;
    padding: 0 20px;
  }
  .contact-item {
    display: flex; align-items: center; gap: 10px;
    font-family: "Barlow Condensed", sans-serif; font-weight: 700;
    font-size: 27px; color: var(--white);
  }
  .contact-icon { width: 30px; height: 30px; }
</style>
</head>
<body>
<main class="rack-card">
  <div class="hero-photo" role="img" aria-label="Photo of a golfer addressing the ball on a sunny fairway lined with trees"></div>
  <svg class="hero-curve" viewBox="0 0 553 120" aria-hidden="true">
    <path d="M0 70 C150 40 300 20 553 25 L553 120 L0 120 Z" fill="#ffffff"/>
    <path d="M0 40 C90 70 200 62 320 45 C420 30 500 20 553 28 L553 22 C480 14 400 22 320 36 C200 56 100 66 0 28 Z" fill="#1f54a8"/>
  </svg>
  <div class="lower-fade"></div>

  <h1 class="title">SUMMER RATES</h1>
  <p class="dates">MAY 1 - SEPTEMBER 30</p>

  <div class="club-seal">The Harbor Pines Golf Club</div>

  <h2 class="rate-tab tab-full">18 HOLES WITH CART</h2>
  <ul class="rate-list rates-full">
    <li>7am – 11am ..............<b>$24</b></li>
    <li>11am – 3pm ............<b>$19</b></li>
    <li>3pm – close ..............<b>$15</b></li>
  </ul>

  <p class="children-note">CHILDREN 15 AND UNDER FREE WITH PAID ADULT</p>

  <h2 class="rate-tab tab-nine">9 HOLES WITH CART $15</h2>
  <ul class="rate-list rates-nine">
    <li>Walking ......................<b>$12</b></li>
  </ul>

  <p class="lunch">LUNCH AVAILABLE DAILY:&nbsp; 10AM – 3PM</p>

  <address class="address-band">
    The Harbor Pines Golf Club<br>
    2450 SW Cedar Marsh Rd Palm Vale, FL 34890
  </address>

  <div class="contact-bar">
    <span class="contact-item">
      <svg class="contact-icon" viewBox="0 0 30 30" aria-hidden="true">
        <circle cx="15" cy="15" r="14" fill="#0d2a5c"/>
        <circle cx="15" cy="15" r="11" fill="none" stroke="#fff" stroke-width="1.2"/>
        <path d="M11 9 C9 12 10 18 14 21 L16 19.5 L14.5 17 L13 17.5 C12 16 12 13.5 12.5 12 L14 12 L14 9.5 Z" fill="#fff"/>
      </svg>
      561-555-0182
    </span>
    <span class="contact-item">
      <svg class="contact-icon" viewBox="0 0 30 30" aria-hidden="true">
        <circle cx="15" cy="15" r="14" fill="#0d2a5c"/>
        <g fill="none" stroke="#fff" stroke-width="1.3">
          <circle cx="15" cy="15" r="9"/>
          <ellipse cx="15" cy="15" rx="4" ry="9"/>
          <line x1="6" y1="15" x2="24" y2="15"/>
          <line x1="8" y1="10" x2="22" y2="10"/>
          <line x1="8" y1="20" x2="22" y2="20"/>
        </g>
      </svg>
      HARBORPINESGC.COM
    </span>
  </div>
</main>
</body>
</html>
```